Kesso Tea Premium Matcha brand Label

This is a label design project for a luxury tea brand. Feel free to be creative within the guidelines.
Attached to this project is a document called “Private Label Design Requirements” with the design guidelines and template. There is another document called "Kesso Tea Packaging Instructions" this has more details necessary to stick to the guidelines in the first document.

I have also attached the certifications to be included as well as different variations of the logo for you to use.

If you have any questions, I am here.
Updates

Need extra days to review

Target Market(s)

Young, active, fun, enjoy the finer things

```html
<!DOCTYPE html>
<html lang="en">
<head>
<meta charset="utf-8">
<title>Kesso Tea — Premium Organic Ceremonial Matcha Label</title>
<link href="https://fonts.googleapis.com/css2?family=Barlow+Condensed:wght@500;600;700&display=swap" rel="stylesheet">
<style>
  :root {
    --backdrop: #f2f1ef;
    --forest: #1f5e43;
    --forest-mid: #2b7653;
    --forest-deep: #184c37;
    --leaf-panel: #cdeacf;
    --leaf-panel-edge: #b7dfbd;
    --meadow: #45a868;
    --lime-band: #8fd47f;
    --ink-green: #16432f;
    --paper: #ffffff;
  }
  * { box-sizing: border-box; margin: 0; padding: 0; }
  html, body {
    width: 1200px;
    height: 833px;
    overflow: hidden;
    background: var(--backdrop);
    font-family: "Barlow Condensed", "Arial Narrow", sans-serif;
  }
  .canvas {
    position: relative;
    width: 1200px;
    height: 833px;
  }
  .label {
    position: absolute;
    left: 220px;
    top: 146px;
    width: 760px;
    height: 540px;
    overflow: hidden;
    background: var(--forest);
  }
  .label__pattern {
    position: absolute;
    inset: 0;
    background:
      radial-gradient(ellipse at 60% 35%, rgba(255,255,255,0.07), transparent 60%),
      linear-gradient(90deg, var(--forest-mid) 0%, var(--forest) 45%, var(--forest-deep) 100%);
  }
  .brand-panel {
    position: absolute;
    left: 24px;
    top: 0;
    width: 196px;
    height: 225px;
    background: linear-gradient(180deg, var(--leaf-panel) 0%, var(--leaf-panel-edge) 100%);
    display: flex;
    align-items: center;
    justify-content: center;
    gap: 10px;
  }
  .brand-panel__dot {
    width: 14px;
    height: 14px;
    border-radius: 50%;
    background: var(--forest);
  }
  .brand-panel__name {
    font-weight: 600;
    font-size: 34px;
    color: var(--forest);
  }
  .weight-panel {
    position: absolute;
    left: 24px;
    top: 225px;
    width: 196px;
    height: 195px;
    background: var(--meadow);
    color: var(--paper);
    padding: 26px 0 0 30px;
    font-weight: 600;
  }
  .weight-panel__label { font-size: 32px; line-height: 1; }
  .weight-panel__grams { font-size: 62px; line-height: 1.05; font-weight: 700; }
  .weight-panel__ounces { font-size: 28px; line-height: 1.1; font-weight: 500; }
  .product-title {
    position: absolute;
    left: 220px;
    top: 170px;
    width: 520px;
    text-align: center;
    font-weight: 600;
    font-size: 118px;
    line-height: 1;
    letter-spacing: 3px;
    color: var(--paper);
  }
  .product-band {
    position: absolute;
    left: 220px;
    top: 330px;
    width: 520px;
    height: 92px;
    background: var(--lime-band);
    padding: 10px 0 0 34px;
    color: var(--ink-green);
    font-weight: 700;
    font-size: 38px;
    line-height: 1.02;
    letter-spacing: 2px;
  }
</style>
</head>
<body>
  <main class="canvas">
    <section class="label">
      <div class="label__pattern" role="img" aria-label="Deep green background with a faint scattered tea leaf pattern"></div>

      <div class="brand-panel">
        <span class="brand-panel__dot"></span>
        <span class="brand-panel__name">Kesso Tea</span>
      </div>

      <div class="weight-panel">
        <p class="weight-panel__label">Net Wt:</p>
        <p class="weight-panel__grams">30g</p>
        <p class="weight-panel__ounces">1.06oz</p>
      </div>

      <h1 class="product-title">KESSO TEA</h1>

      <div class="product-band">
        <p>PREMIUM ORGANIC</p>
        <p>CEREMONIAL MATCHA</p>
      </div>
    </section>
  </main>
</body>
</html>
```